ONE PAGE WEBSITE for Zesty Recruitment Agency

Hello creative gurus,

We're are after a ONE PAGE World Press web design.

We're a recruitment start-up specializing in Information Technology.

The design should be cool, quirky and NOT mainstream.

The kind of web designs we like:

http://www.vantorix.co.za/#what-we-do
http://quillandmoss.com/
http://www.kelvado.com/index.html#home
http://marcellobrantovi.com/#/selected-works

And, we only like the front page of this web site: http://www.zenbyglim.com/

Any questions, please do let us know!

Thank you, and happy creating!

Robin

Reason: Just need a day or two to finalize everything. Thanks, Robin

Target Market(s)

Companies, employees, candidates

Industry/Entity Type

Recruitment

Coding

Coded - Design and coding required

Colors
f37122
f68e4e
ffcf3e
00a990
86cfc6
fcca95
fee18a

Requirements
Must have
• 1. The website should be techy, cool, funky, quirky and user-friendly.
• 2. Mobile-compatible
• 3. Please use our spaceman logo through the website (attached).
• 4. Please see attached website content/brief.
• 5. Colors - orange color is a must, but please use other colors to spice it up - make it more fun.
• The kind of web designs we like:
• http://www.vantorix.co.za/#what-we-do
• http://quillandmoss.com/
• http://www.kelvado.com/index.html#home
• http://marcellobrantovi.com/#/selected-works
• http://www.zenbyglim.com/
• Any questions, please do let us know!
Should not have
• -NO stock image banners, photos, images

```html
<!DOCTYPE html>
<html lang="en">
<head>
<meta charset="utf-8">
<title>Zenkora Talent</title>
<link href="https://fonts.googleapis.com/css2?family=Ubuntu:wght@300;400;500;700&display=swap" rel="stylesheet">
<style>
:root{
  --orange:#f37122;
  --orange-bright:#ff6a00;
  --ink:#2b2b2b;
  --text:#555;
  --muted:#888;
  --light:#f7f7f7;
  --footer:#f4f4f4;
  --white:#fff;
  --purple:#9b00c8;
  --lime:#97e100;
  --hero-dark:#3a3a3a;
  --blog-dark:#4a4a4a;
}
*{box-sizing:border-box;margin:0;padding:0}
html,body{width:1200px;height:3152px;overflow:hidden}
body{font-family:'Ubuntu',sans-serif;color:var(--text);background:var(--white);position:relative}
section,header,footer{position:absolute;left:0;width:1200px}
.center{text-align:center}
.section-title{color:var(--orange);font-size:20px;font-weight:500;text-align:center;letter-spacing:.5px}

/* header */
.site-header{top:0;height:88px;background:var(--white)}
.brand{position:absolute;left:220px;top:26px;display:flex;align-items:center;gap:8px}
.brand-dot{width:30px;height:30px;border-radius:50%;background:var(--ink)}
.brand-name{font-size:17px;font-weight:700;color:var(--ink);letter-spacing:1px}
.main-nav{position:absolute;right:222px;top:38px;display:flex;gap:22px;font-size:12px;font-weight:500;color:var(--ink)}

/* hero */
.hero{top:88px;height:454px;background:linear-gradient(180deg,#595959 0%,#3e3e3e 55%,#2d2d2d 100%)}
.hero-title{position:absolute;top:242px;width:100%;text-align:center;color:var(--white);font-size:21px;font-weight:300}
.hero-btn{position:absolute;left:500px;top:294px;width:200px;height:40px;border:1px solid var(--white);color:var(--white);font-size:12px;line-height:38px;text-align:center}
.hero-dots{position:absolute;top:403px;left:0;width:100%;display:flex;justify-content:center;gap:11px}
.hero-dots span{width:8px;height:8px;border-radius:50%;background:var(--white)}
.hero-dots span:first-child{background:var(--orange)}

/* welcome */
.welcome{top:542px;height:268px}
.welcome .section-title{margin-top:72px}
.welcome p{width:760px;margin:38px auto 0;font-size:10.5px;line-height:21px;text-align:center;color:var(--text)}

/* why */
.why{top:810px;height:585px;background:var(--light)}
.why .section-title{margin-top:56px}
.reason{position:absolute;width:320px;font-size:13px;line-height:21px;color:var(--text)}
.reason svg{position:absolute;left:-40px;top:3px}
.r1{left:286px;top:132px}.r2{left:673px;top:132px}
.r3{left:286px;top:272px}.r4{left:673px;top:272px}
.why-note{position:absolute;top:432px;width:100%;text-align:center;font-size:12.5px;line-height:22px;color:var(--muted)}
.why-call{position:absolute;top:494px;width:100%;text-align:center;font-size:17px;font-weight:500;color:var(--ink)}

/* about */
.about{top:1395px;height:665px}
.about .section-title{margin-top:62px}
.avatar{position:absolute;left:527px;top:129px;width:146px;height:146px;border-radius:50%;background:radial-gradient(circle at 50% 40%,#d9c3b3,#8b8fa3 75%)}
.greeting{position:absolute;top:313px;width:100%;text-align:center;font-size:17px;font-weight:500;color:var(--ink)}
.about-copy{position:absolute;top:368px;left:240px;width:720px;font-size:10.5px;line-height:21px;text-align:center;color:var(--ink)}
.divider{position:absolute;top:516px;left:296px;width:608px;height:1px;background:#ddd}
.about-small{position:absolute;top:550px;width:100%;text-align:center;font-size:10.5px;color:var(--ink)}
.about-big{position:absolute;top:567px;width:100%;text-align:center;font-size:18px;color:var(--ink)}

/* blog */
.blog{top:2060px;height:517px;background:linear-gradient(160deg,#6b6b6b 0%,var(--blog-dark) 45%,#2e2e2e 100%)}
.blog .section-title{color:var(--white);font-weight:400;margin-top:86px}
.post{position:absolute;top:166px;width:240px;height:204px;padding:26px 20px;color:var(--white)}
.post h3{font-size:16px;font-weight:400;line-height:20px;text-transform:uppercase}
.post-date{position:absolute;left:20px;top:150px;font-size:11px;font-weight:700}
.post-by{position:absolute;left:20px;top:168px;font-size:8px}
.post-more{position:absolute;right:8px;top:150px;width:64px;height:24px;font-size:9px;line-height:24px;text-align:center;color:var(--white)}
.p1{left:220px;background:var(--purple)}.p1 .post-more{background:#5e007a}
.p2{left:479px;background:var(--lime)}.p2 .post-more{background:#5d8c00}
.p3{left:741px;background:var(--orange-bright)}.p3 .post-more{background:#a84300}
.blog-btn{position:absolute;left:500px;top:397px;width:200px;height:38px;border:1px solid var(--white);color:var(--white);font-size:12px;line-height:36px;text-align:center}

/* contact */
.contact{top:2577px;height:370px}
.contact .section-title{margin-top:52px}
.contact-intro{position:absolute;top:104px;left:190px;width:820px;text-align:center;font-size:16px;line-height:28px;color:var(--muted)}
.channel{position:absolute;top:212px;width:240px;text-align:center}
.channel svg{display:block;margin:0 auto}
.channel .label{font-size:11px;color:var(--text);margin-top:12px}
.channel .value{font-size:19px;color:var(--text);margin-top:12px}
.c1{left:216px}.c2{left:480px}.c3{left:750px}
.socials{display:flex;justify-content:center;gap:14px;margin-top:14px}
.socials span{width:13px;height:13px;border-radius:50%;background:#999}

/* footer */
.site-footer{top:2947px;height:205px;background:var(--footer)}
.footer-brand{position:absolute;top:50px;width:100%;display:flex;justify-content:center;align-items:center;gap:8px}
.footer-nav{position:absolute;top:113px;width:100%;display:flex;justify-content:center;gap:24px;font-size:11.5px;color:var(--ink)}
.copyright{position:absolute;top:146px;width:100%;text-align:center;font-size:11px;color:var(--ink);letter-spacing:.3px}
</style>
</head>
<body>

<header class="site-header">
  <div class="brand"><span class="brand-dot"></span><span class="brand-name">ZENKORA</span></div>
  <nav class="main-nav"><span>HOME</span><span>COMPANIES</span><span>TALENT REFERALS</span><span>ABOUT US</span><span>BLOG</span><span>CONTACT US</span></nav>
</header>

<section class="hero" role="img" aria-label="Black and white aerial photograph of a city skyline">
  <h1 class="hero-title">We're a recruitment company specializing in Information Technology.</h1>
  <div class="hero-btn">GET STARTED TODAY</div>
  <div class="hero-dots"><span></span><span></span><span></span><span></span></div>
</section>

<section class="welcome">
  <h2 class="section-title">WELCOME TO ZENKORA TALENT</h2>
  <p>We're Sydney's IT talent specialists. We are passionate, with boundless energy, and work to bring great people together. We specialise in permanent and contract recruitment solutions across Information Technology. We exist to place talented developers in jobs they love, and to help companies find, attract and retain the most qualified talent in the marketplace.<br>To achieve this, we run an ethical agency (yes a recruiter that's ethical, shock / horror we know!), and are extremely active in the community.</p>
</section>

<section class="why">
  <h2 class="section-title">WHY WORK WITH US ?</h2>
  <div class="reason r1"><svg width="22" height="16" viewBox="0 0 22 16"><path d="M2 8l6 6L20 2" fill="none" stroke="#f37122" stroke-width="4"/></svg>We're experts in our field and have years of hands-on experience in the I.T. industry. We know our market intimately and understand the unique skills required to build a successful I.T. team.</div>
  <div class="reason r2"><svg width="22" height="16" viewBox="0 0 22 16"><path d="M2 8l6 6L20 2" fill="none" stroke="#f37122" stroke-width="4"/></svg>We offer a bespoke service with dedicated account manager (a nice one!) who will stay in regular contact with you.</div>
  <div class="reason r3"><svg width="22" height="16" viewBox="0 0 22 16"><path d="M2 8l6 6L20 2" fill="none" stroke="#f37122" stroke-width="4"/></svg>We walk in your shoes. We've been on the other side of the recruitment process - your side (wether you're a talent or an employer), and we understand the challenges you're</div>
  <div class="reason r4"><svg width="22" height="16" viewBox="0 0 22 16"><path d="M2 8l6 6L20 2" fill="none" stroke="#f37122" stroke-width="4"/></svg>We're nice. We're ethical. We'll even bring you your favourite coffee, hot chocolate, beer (whatever makes you tick) when we come to meet you!</div>
  <p class="why-note">Whether you're a client looking to fill a vacancy, or a candidate searching for your next move, we can help you. We're a friendly bunch and we'd<br>be happy to chat to you about working together.</p>
  <p class="why-call">Call us on 0207 555 0142 or say “hello” at info@zenkoratalent.com.</p>
</section>

<section class="about">
  <h2 class="section-title">ABOUT US</h2>
  <div class="avatar" role="img" aria-label="Portrait photograph of the company co-founder"></div>
  <p class="greeting">Hi I'm Helena,</p>
  <p class="about-copy">I'm a co-founder of Zenkora Talent since 2016 and have loved every minute of it. Our mission is to help great developers &amp; companies connect. With more than 25 years' combined experience in IT, communication and customer service, we're confident we can help you. Whether you're a job seeker or an employer, we understand the challenges you face. How come, you may ask? We walked in your shoes throughout our careers with some roads being quite bumpy. In our time, we noticed a trend in recruiters' chasing commissions and in the process neglecting client and candidate's needs, providing poor customer service, and deluging inbox with unsuitable candidates. So we built Zenkora Talent to do exactly the opposite. We're glad our experience with some of the recruitment agencies was bumpy (really, thank you very much!), otherwise we wouldn't have started Zenkora, met some amazing people and learnt so much in the process.</p>
  <div class="divider"></div>
  <p class="about-small">I'd love to tell you more about our approach, so have a look around and get in touch if you have any</p>
  <p class="about-big">Questions on 0207 555 0142 or via info@zenkoratalent.com.</p>
</section>

<section class="blog" role="img" aria-label="Dark black and white photograph of hands typing on a keyboard">
  <h2 class="section-title">BLOG</h2>
  <article class="post p1"><h3>Neque porro quisquam est qui dolorem ipsum quia dolor adipisci velit...</h3><div class="post-date">JANUARY 21TH | 2017</div><div class="post-by">Posted By Zenkora Talent</div><div class="post-more">MORE</div></article>
  <article class="post p2"><h3>Neque porro quisquam est qui dolorem ipsum quia dolor adipisci velit...</h3><div class="post-date">JANUARY 21TH | 2017</div><div class="post-by">Posted By Zenkora Talent</div><div class="post-more">MORE</div></article>
  <article class="post p3"><h3>Neque porro quisquam est qui dolorem ipsum quia dolor adipisci velit...</h3><div class="post-date">JANUARY 21TH | 2017</div><div class="post-by">Posted By Zenkora Talent</div><div class="post-more">MORE</div></article>
  <div class="blog-btn">READ MORE ON OUR BLOG</div>
</section>

<section class="contact">
  <h2 class="section-title">CONTACT US</h2>
  <p class="contact-intro">If you'd like to discover more about how we work, then please do get in touch. We're a friendly bunch and we'd be happy to chat to you about working together!</p>
  <div class="channel c1">
    <svg width="26" height="26" viewBox="0 0 24 24"><path d="M6.6 2.5l3 3.6-1.9 2.2c1.2 2.6 3.3 4.8 6 6l2.2-1.9 3.6 3-1.8 3.1C10.5 18 6 13.5 3.5 6.3z" fill="#f37122"/></svg>
    <div class="label">Telephone</div><div class="value">0299 555 010</div>
  </div>
  <div class="channel c2">
    <svg width="30" height="24" viewBox="0 0 30 24"><rect x="2" y="3" width="26" height="18" fill="none" stroke="#f37122" stroke-width="2.5"/><path d="M2 3l13 10L28 3" fill="none" stroke="#f37122" stroke-width="2.5"/></svg>
    <div class="label">E-mail</div><div class="value">info@zenkoratalent.com</div>
  </div>
  <div class="channel c3">
    <svg width="30" height="24" viewBox="0 0 30 24"><ellipse cx="12" cy="9" rx="10" ry="7" fill="none" stroke="#f37122" stroke-width="2.5"/><path d="M20 12c4 1 7 3 7 6l1 4-4-2" fill="none" stroke="#f37122" stroke-width="2.5"/></svg>
    <div class="label">Stay social</div>
    <div class="socials"><span></span><span></span><span></span></div>
  </div>
</section>

<footer class="site-footer">
  <div class="footer-brand"><span class="brand-dot"></span><span class="brand-name">ZENKORA</span></div>
  <nav class="footer-nav"><span>HOME</span><span>COMPANIES</span><span>TALENT REFERALS</span><span>ABOUT US</span><span>BLOG</span><span>CONTACT US</span></nav>
  <p class="copyright">© 2017 COMPANY NAME | ALL RIGHTS RESERVED</p>
</footer>

</body>
</html>
```